Quorva - corporate Business Card

We need a good look and innovative business card for a new start up company based in Los Angeles called "Quorva". We are in a payment business, including payment card, app, and ewallet. We are expert in online payment and Card not present (CNP) transaction.
We need an innovative, modern business card.

Our logo font is Aero Matics

Target Market(s)

Startup - Bank - Online Payment - Card Manufacturing

Industry/Entity Type

Startup

Contact Information for Business Card

phone: 555 014 7396 - Address: 4172 Marlowe blvd, Brenhaven, OR 97299

Requirements
Must have
• Message: innovative, professional, expert, high tech, trust, online payment expert, security
Nice to have
• no comment
Should not have
• no Comment

```html
<!DOCTYPE html>
<html lang="en">
<head>
<meta charset="utf-8">
<title>Quorva – Business Card</title>
<link rel="stylesheet" href="https://fonts.googleapis.com/css2?family=Exo+2:wght@600&family=Source+Sans+3:wght@400;700&display=swap">
<style>
  :root {
    --brand-red: #b81f31;
    --paper: #ffffff;
    --ink: #3a3a3a;
    --backdrop: #e9e6e2;
  }
  * { box-sizing: border-box; margin: 0; padding: 0; }
  html, body {
    width: 1200px; height: 900px; overflow: hidden;
    background: var(--backdrop);
  }
  .stage {
    position: relative; width: 1200px; height: 900px;
    display: flex; flex-direction: column; align-items: center; justify-content: center; gap: 40px;
  }
  .card {
    position: relative; width: 680px; height: 388px; overflow: hidden;
    box-shadow: 0 6px 18px rgba(0,0,0,0.18);
  }

  /* Back side */
  .card--back { background: var(--brand-red); color: var(--paper); }
  .back-brand {
    position: absolute; left: 0; right: 0; top: 112px;
    display: flex; align-items: center; justify-content: center; gap: 16px;
  }
  .back-brand__disc {
    width: 116px; height: 116px; border-radius: 50%; background: var(--paper); flex: none;
  }
  .back-brand__name {
    font-family: "Exo 2", sans-serif; font-weight: 600; font-size: 76px;
    letter-spacing: 2px; line-height: 1; color: var(--paper);
  }
  .values {
    position: absolute; left: 0; right: 0; top: 260px;
    font-family: "Source Sans 3", sans-serif; font-size: 17px; letter-spacing: 0.6px;
    text-align: center; line-height: 1.6;
  }
  .values li { display: inline; list-style: none; }
  .values li::before { content: "\25CF"; font-size: 11px; margin: 0 6px 0 10px; vertical-align: 2px; }

  /* Front side */
  .card--front { background: var(--paper); }
  .front-disc {
    position: absolute; left: 468px; top: 58px;
    width: 380px; height: 380px; border-radius: 50%; background: var(--brand-red);
  }
  .front-name {
    position: absolute; left: 52px; top: 52px;
    font-family: "Exo 2", sans-serif; font-weight: 600; font-size: 88px;
    letter-spacing: 3px; line-height: 1; color: var(--brand-red);
  }
  .person { position: absolute; left: 56px; top: 178px; font-family: "Source Sans 3", sans-serif; }
  .person__name {
    font-weight: 700; font-size: 24px; letter-spacing: 1px; color: var(--brand-red); text-transform: uppercase;
  }
  .person__role { font-size: 19px; color: var(--ink); margin-top: -2px; }
  .contact {
    position: absolute; left: 56px; top: 262px; list-style: none;
    font-family: "Source Sans 3", sans-serif; font-size: 19px; color: var(--ink); line-height: 1.35;
  }
  .contact li { display: flex; align-items: flex-start; gap: 10px; }
  .contact svg { width: 16px; height: 16px; margin-top: 4px; flex: none; fill: var(--brand-red); }
</style>
</head>
<body>
<main class="stage">

  <section class="card card--back" aria-label="Card back">
    <div class="back-brand">
      <span class="back-brand__disc"></span>
      <span class="back-brand__name">quorva</span>
    </div>
    <ul class="values">
      <li>INNOVATIVE</li><li>PROFESSIONA EXPERT</li><li>HIGH TECH</li><li>TRUST</li><br>
      <li>ONLINE PAYMENT EXPERT</li><li>SECURITY</li>
    </ul>
  </section>

  <section class="card card--front" aria-label="Card front">
    <span class="front-disc"></span>
    <div class="front-name">quorva</div>
    <div class="person">
      <div class="person__name">Daniel Reyes</div>
      <div class="person__role">Managing Director</div>
    </div>
    <ul class="contact">
      <li>
        <svg viewBox="0 0 16 16" aria-hidden="true"><path d="M3.6 1.2l2.3 2.4-1.3 1.9c.9 2 2.5 3.6 4.5 4.6l1.9-1.3 2.4 2.3-1.2 2.3C7 13.1 2.9 9 1.6 3.8z"/></svg>
        <span>555 014 7396</span>
      </li>
      <li>
        <svg viewBox="0 0 16 16" aria-hidden="true"><path d="M8 1a7 7 0 1 0 0 14A7 7 0 0 0 8 1zm-1 2.2c-.3 1-1.6 1.2-1.4 2.4.2 1 1.6.8 1.8 1.9.2 1-1 1.6-.5 2.6.4.9 1.1 1.6.9 2.8A5 5 0 0 1 7 3.2zm3.3 8.8c-.4-.9.5-1.7-.1-2.5-.6-.7-1.7-.3-1.9-1.3-.1-.9 1.2-1.3 1.5-2.2a5 5 0 0 1 .5 6z"/></svg>
        <span>www.quorva.com</span>
      </li>
      <li>
        <svg viewBox="0 0 16 16" aria-hidden="true"><path d="M8 1a5 5 0 0 0-5 5c0 3.6 5 9 5 9s5-5.4 5-9a5 5 0 0 0-5-5zm0 7a2 2 0 1 1 0-4 2 2 0 0 1 0 4z"/></svg>
        <span>4172 Marlowe blvd,<br>Brenhaven, OR 97299</span>
      </li>
    </ul>
  </section>

</main>
</body>
</html>
```